Fleyer für Rasenroboter-Garage
Zielgruppe
Aluminiumsysteme
Aufgabenstellung
Für ein neues Produkt " Rasenroboter-Garage" einen Fleyer entwerfen. Format DinA4 Vorder und Rückseite. Bilder der Garage sind als Anhang anbei.Es gibt eine Basic Version mit Dach und eine Expert Version mit Dach und Seitenverkleidung. Sogan " Das Zuhause für Ihren Rasenroboter" . Merkmale sind hochertige Materialien, qualitative Verarbeitung, ästhetisches Design,lange Lebensdauer.

```html
<!DOCTYPE html>
<html lang="de">
<head>
<meta charset="utf-8">
<title>GaraBot – Flyer Rasenroboter-Garage</title>
<link href="https://fonts.googleapis.com/css2?family=Arimo:wght@400;700&family=Exo+2:wght@500;600&family=Roboto+Condensed:ital,wght@1,900&display=swap" rel="stylesheet">
<style>
  :root {
    --backdrop: #e4e4e4;
    --ink: #111111;
    --header-black: #0b0b0b;
    --logo-green: #6cbf2a;
    --price-green: #2f7a1d;
    --tag-yellow: #ffe81a;
    --panel-light: #f1f1f1;
    --panel-shade: #dcdcdc;
    --grass-dark: #3f7a1c;
    --grass-light: #74b33a;
    --white: #ffffff;
  }
  * { margin: 0; padding: 0; box-sizing: border-box; }
  html, body { width: 1000px; height: 1200px; overflow: hidden; }
  body { background: var(--backdrop); font-family: "Arimo", Arial, sans-serif; color: var(--ink); }

  .flyer {
    position: absolute; left: 98px; top: 30px;
    width: 804px; height: 1140px;
    background: var(--panel-light);
    overflow: hidden;
  }

  .header {
    position: absolute; left: 0; top: 0; width: 100%; height: 102px;
    background: var(--header-black);
    display: flex; align-items: center;
  }
  .brand { position: absolute; left: 77px; top: 30px; display: flex; align-items: center; gap: 12px; }
  .brand-mark { width: 34px; height: 34px; background: var(--logo-green); }
  .brand-name { font-weight: 700; font-size: 34px; color: var(--logo-green); letter-spacing: 1px; }
  .tagline {
    position: absolute; left: 341px; top: 30px;
    font-family: "Exo 2", sans-serif; font-weight: 500; font-size: 31px; color: var(--white);
  }

  .lawn {
    position: absolute; left: 0; top: 102px; width: 100%; height: 981px;
    background: linear-gradient(180deg, var(--grass-light) 0%, var(--grass-dark) 30%, var(--grass-light) 45%, var(--grass-dark) 70%, var(--grass-light) 100%);
  }
  .panels { position: absolute; left: 0; top: 0; width: 804px; height: 1140px; }

  .product-photo {
    position: absolute;
    background: linear-gradient(180deg, #3e6b52 0%, #2d5a43 35%, #b8403a 65%, #d9d9d9 100%);
  }
  .product-photo.basic { left: 375px; top: 185px; width: 366px; height: 224px; }
  .product-photo.expert { left: 375px; top: 639px; width: 406px; height: 271px;
    background: linear-gradient(180deg, #3b6650 0%, #2c5842 55%, #c8423a 80%, #dcdcdc 100%); }

  .version-tag {
    position: absolute;
    background: var(--tag-yellow);
    font-family: "Exo 2", sans-serif; font-weight: 600; font-size: 27px;
    color: var(--ink);
    padding: 9px 22px;
    transform: rotate(-3deg);
    box-shadow: 2px 3px 4px rgba(0,0,0,.35);
  }
  .version-tag.basic { left: 37px; top: 311px; }
  .version-tag.expert { left: 50px; top: 761px; }

  .offer { position: absolute; left: 47px; width: 440px; }
  .offer.basic { top: 416px; }
  .offer.expert { top: 845px; }
  .offer-title { font-size: 15px; font-weight: 700; line-height: 19px; margin-bottom: 9px; }
  .offer-text { font-size: 13.5px; line-height: 18px; margin-bottom: 14px; }
  .offer-specs { font-size: 10.5px; line-height: 13.5px; }
  .offer-specs b { font-weight: 700; }

  .price {
    position: absolute;
    font-family: "Roboto Condensed", sans-serif; font-style: italic; font-weight: 900;
    color: var(--price-green);
    font-size: 128px; line-height: 1; letter-spacing: -3px;
    -webkit-text-stroke: 4px var(--white);
    paint-order: stroke fill;
    text-shadow: 4px 6px 6px rgba(0,0,0,.35);
  }
  .price sup { font-size: 60px; vertical-align: 52px; letter-spacing: -1px; }
  .price.basic { left: 545px; top: 378px; }
  .price.expert { left: 543px; top: 884px; }

  .contact-line {
    position: absolute; left: 0; top: 1040px; width: 100%;
    text-align: center; font-weight: 700; font-size: 19.5px;
  }
  .footer {
    position: absolute; left: 0; top: 1083px; width: 100%; height: 57px;
    background: linear-gradient(180deg, #3a3a3a 0%, #0a0a0a 100%);
    color: var(--white); font-weight: 700; font-size: 24.5px;
    display: flex; align-items: center; justify-content: center;
  }
</style>
</head>
<body>
  <main class="flyer">
    <header class="header">
      <div class="brand">
        <span class="brand-mark"></span>
        <span class="brand-name">GaraBot</span>
      </div>
      <div class="tagline">Ein Gerät. Eine Garage.</div>
    </header>

    <div class="lawn" role="img" aria-label="Foto einer grünen, gemähten Rasenfläche"></div>

    <svg class="panels" viewBox="0 0 804 1140" aria-hidden="true">
      <defs>
        <linearGradient id="panelFill" x1="0" y1="0" x2="0" y2="1">
          <stop offset="0" stop-color="#ffffff"/>
          <stop offset="1" stop-color="#e2e2e2"/>
        </linearGradient>
      </defs>
      <polygon points="0,355 804,322 804,558 0,574" fill="url(#panelFill)"/>
      <polygon points="0,785 804,753 804,1083 0,1083" fill="url(#panelFill)"/>
    </svg>

    <div class="product-photo basic" role="img" aria-label="Produktfoto: grüne Basic-Garage mit Dach über einem roten Mähroboter"></div>
    <div class="product-photo expert" role="img" aria-label="Produktfoto: grüne Expert-Garage mit Dach und Seitenverkleidung, darin ein roter Mähroboter"></div>

    <div class="version-tag basic">Basic Version</div>
    <section class="offer basic">
      <h2 class="offer-title">Die günstige Alternative mit Dach!</h2>
      <p class="offer-text">Lorem ipsum dolor sit amet, consetetur sadipscing elitr, sed diam nonumy eirmod tempor invidunt ut labore et dolore magna aliquyam erat, sed diam voluptua.</p>
      <p class="offer-specs"><b>Material:</b> Kunststoff<br><b>Maße:</b> 800 mm (Länge) x 500 mm – 570 mm (lichte Breite) x 430mm (Höhe)<br><b>Gewicht:</b> 3,2kg</p>
    </section>
    <div class="price basic">49.<sup>99</sup></div>

    <div class="version-tag expert">Expert Version</div>
    <section class="offer expert">
      <h2 class="offer-title">Der ideale Rasenmäherschutz mit<br>Dach und Seitenverkleidung!</h2>
      <p class="offer-text">Lorem ipsum dolor sit amet, consetetur sadipscing elitr, sed diam nonumy eirmod tempor invidunt ut labore et dolore magna aliquyam erat, sed diam voluptua.</p>
      <p class="offer-specs"><b>Material:</b> Kunststoff<br><b>Maße:</b> 800 mm (Länge) x 500 mm – 570 mm (lichte Breite) x 430mm (Höhe)<br><b>Gewicht:</b> 3,5kg</p>
    </section>
    <div class="price expert">99.<sup>99</sup></div>

    <p class="contact-line">Kontaktieren Sie uns bei offenen Fragen, wir helfen Ihnen gerne weiter!</p>
    <footer class="footer">Telefon: 0221 555012-0 • E-Mail: info@garabot-beispiel.de</footer>
  </main>
</body>
</html>
```